9x12 Business Brochure, 3 fold, for Internet Marketing Company

I'd like to have a brochure designed for my Internet marketing company. I have the content all ready, 10 Internet Marketing Myths, which you can see here: http://www.brisklanternstudio.example/usual-web-promotion-fables/. I'm looking for something creative and business to business. The company is all about Internet marketing. I like the "http://" header I use at our website. People like it too and identify with it. Audience is business owners 35 to 55 years old. I use blue at my website. I *think* I would like the cover page (front page) to open with some attention grabbing text, that basically takes most of the front page of the brochure. It would probably say: "I Can Help You Get BETTER RESULTS from Your Website, More Traffic, TOP RANKINGS at Quorble, More Leads and MORE SALES. But first you'll have to avoid these common Internet marketing myths..." The inside pages would have the content from above (the 10 myths). The back page would have testimonials that I can provide. And the inside folded in page (or what I call the inside folded in page) would have a list of services. I think I want the dimensions 12x9 which is a larger sized, three-fold brochure.

Target Market(s)

I use this brochure to send to business owners and managers to show them I know what I'm talking about and and expert. See attachment for content.

Industry/Entity Type

Marketing

Requirements
Should not have
• No clipart. Probably not illustrations. Photos. The "http://" used at the site is something people "connect" with and get that this is about Internet marketing.

```html
<!DOCTYPE html>
<html lang="en">
<head>
<meta charset="utf-8">
<title>Brisk Lantern Marketing – Tri-fold Brochure</title>
<link href="https://fonts.googleapis.com/css2?family=Didact+Gothic&family=Open+Sans:ital,wght@0,400;0,700;1,700&family=Arimo:ital,wght@0,400;0,700;1,400&display=swap" rel="stylesheet">
<style>
:root{
  --backdrop:#6f6f6f;
  --paper:#ffffff;
  --paper-shade:#e6e9f2;
  --navy:#1e2f8c;
  --royal:#2b4fc4;
  --sky:#139fe0;
  --yellow:#ffe600;
  --ink:#333333;
  --name-blue:#2a2e8f;
}
*{margin:0;padding:0;box-sizing:border-box}
html,body{width:1200px;height:899px;overflow:hidden;background:var(--backdrop)}
.canvas{position:relative;width:1200px;height:899px}
.panel-shapes{position:absolute;left:0;top:0}
.tab-title{position:absolute;font:700 22px/1 "Open Sans",sans-serif;color:#fff}
.services{position:absolute;left:78px;top:124px;list-style:none;font:18px/35.3px "Didact Gothic",sans-serif;color:var(--ink)}
.services li{position:relative;padding-left:20px;white-space:nowrap}
.services li::before{content:"";position:absolute;left:0;top:13px;width:11px;height:11px;
  background:var(--navy);clip-path:polygon(100% 0,30% 20%,55% 42%,0 90%,12% 100%,62% 52%,82% 72%)}
.motto{position:absolute;left:36px;width:376px;top:814px;text-align:center;
  font:italic 700 16.5px/22px "Open Sans",sans-serif;color:var(--yellow)}
.stories{position:absolute;left:434px;top:126px;width:334px;font:10px/12.4px "Didact Gothic",sans-serif;color:var(--ink);text-align:justify}
.stories p{margin-bottom:12px}
.signoff{position:absolute;left:412px;width:376px;top:592px;text-align:center;font:14px/19px Arimo,sans-serif;color:var(--name-blue)}
.signoff strong{display:block;font-size:19px;line-height:24px}
.back-title{position:absolute;left:444px;top:718px;font:700 26px/33px "Open Sans",sans-serif;color:var(--yellow)}
.office{position:absolute;top:804px;font:10.5px/13.4px Arimo,sans-serif;color:#fff}
.front-title{position:absolute;right:66px;top:66px;text-align:right;font:700 38px/50px "Open Sans",sans-serif;color:#fff}
.pitch{position:absolute;left:820px;top:508px;font:22px/36px "Arimo",sans-serif;color:var(--yellow);letter-spacing:-.4px}
.pitch b{font-weight:700;font-size:32px;display:block;line-height:36px}
.pitch .line{display:block}
.teaser{position:absolute;left:820px;top:734px;font:italic 16px/20px Arimo,sans-serif;color:#fff}
.front-contact{position:absolute;left:788px;width:376px;top:794px;text-align:center;font:700 19px/22px Arimo,sans-serif;color:#fff}
.front-url{display:block;margin-top:6px;font:400 14px/18px Arimo,sans-serif;color:var(--yellow)}
</style>
</head>
<body>
<main class="canvas">
<svg class="panel-shapes" width="1200" height="899" viewBox="0 0 1200 899">
  <defs>
    <linearGradient id="paperFade" x1="0" y1="0" x2="1" y2="0">
      <stop offset="0" stop-color="var(--paper-shade)"/><stop offset=".5" stop-color="#fff"/><stop offset="1" stop-color="var(--paper-shade)"/>
    </linearGradient>
    <linearGradient id="bandBlue" x1="0" y1="0" x2="1" y2="1">
      <stop offset="0" stop-color="var(--sky)"/><stop offset="1" stop-color="var(--royal)"/>
    </linearGradient>
    <linearGradient id="coverBlue" x1="0" y1="0" x2="1" y2="1">
      <stop offset="0" stop-color="var(--royal)"/><stop offset=".5" stop-color="var(--sky)"/><stop offset="1" stop-color="var(--navy)"/>
    </linearGradient>
    <linearGradient id="coverLower" x1="0" y1="0" x2="1" y2="1">
      <stop offset="0" stop-color="var(--sky)"/><stop offset=".45" stop-color="var(--royal)"/><stop offset="1" stop-color="var(--navy)"/>
    </linearGradient>
    <linearGradient id="browserTones" x1="0" y1="0" x2="1" y2="1">
      <stop offset="0" stop-color="#eef3fb"/><stop offset=".6" stop-color="#b9cbe6"/><stop offset="1" stop-color="#5f7fb8"/>
    </linearGradient>
  </defs>
  <!-- inside flap: services -->
  <rect x="36" y="26" width="376" height="848" fill="url(#paperFade)"/>
  <polygon points="36,790 412,758 412,874 36,874" fill="url(#bandBlue)"/>
  <polygon points="36,53 306,53 322,98 36,98" fill="url(#bandBlue)"/>
  <path d="M314 74 l20 8 -8 3 6 8 -4 3 -6 -8 -6 6z" fill="var(--navy)"/>
  <!-- back panel: stories -->
  <rect x="412" y="26" width="376" height="848" fill="url(#paperFade)"/>
  <polygon points="412,702 788,666 788,874 412,874" fill="url(#bandBlue)"/>
  <polygon points="412,53 622,53 638,98 412,98" fill="url(#bandBlue)"/>
  <path d="M630 74 l20 8 -8 3 6 8 -4 3 -6 -8 -6 6z" fill="var(--navy)"/>
  <line x1="412" y1="26" x2="412" y2="874" stroke="#c9ccd6"/>
  <!-- cover panel -->
  <rect x="788" y="26" width="376" height="848" fill="url(#coverBlue)"/>
  <polygon points="788,470 1164,430 1164,874 788,874" fill="url(#coverLower)"/>
  <polygon points="788,240 1164,186 1164,432 788,492" fill="url(#browserTones)" role="img" aria-label="Photo: close-up of a browser address bar reading http://www with a mouse pointer"/>
</svg>

<h2 class="tab-title" style="left:70px;top:63px">Services &amp; Expertise</h2>
<ul class="services">
  <li>Internet Strategy Development</li>
  <li>Custom Website Design</li>
  <li>Blog Design &amp; Support</li>
  <li>Online Marketing Copywriting</li>
  <li>Social Media Marketing</li>
  <li>Search Engine Optimization (SEO)</li>
  <li>Conversion Optimization</li>
  <li>Content Marketing Management</li>
  <li>Using Chatterbook for Business</li>
  <li>Quorble+, Vidstream, Pinboardly</li>
  <li>Email Marketing &amp; Production</li>
  <li>Inquiry and Lead Development</li>
  <li>Quorble Bidwords Pay-Per-Click</li>
  <li>Quorble Local Places (maps)</li>
  <li>E-Commerce Development</li>
  <li>High-Performance Hosting</li>
  <li>Security &amp; Contingency Planning</li>
  <li>One-on-One or Group Training</li>
</ul>
<p class="motto">"If you think it's expensive to hire an<br>expert, wait until you hire an amateur."</p>

<h2 class="tab-title" style="left:433px;top:63px">Success Stories</h2>
<div class="stories">
  <p>Quorble Rankings – "... we have spent over a year trying to get onto page one at Quorble. I has been very frustrating and we've wasted a lot of time and money. Dana explained everything very clearly and we did everything he told us. 90 days later we're now showing up on the first page of Quorble!</p>
  <p>Website Design – "We needed a new website that properly reflected our company and the products and services we sell. We started getting more leads within 72 hours of launching the new site Dana and his team designed for us. We're also getting better results from our Quorble Bidwords pay-per-click advertising and more of those clicks are turning into inquiries!"</p>
  <p>More to Come - Lorem ipsum dolor sit amet, consectetur adipiscing elit. Suspendisse justo velit, auctor ut pulvinar a, egestas non urna. Suspendisse potenti. Sed at pellentesque dolor. Vivamus sed nibh nisl. Nunc tortor tellus, facilisis eget pretium vitae, porttitor quis libero.</p>
  <p>More to Come - Lorem ipsum dolor sit amet, consectetur adipiscing elit. Suspendisse justo velit, auctor ut pulvinar a, egestas non urna. Suspendisse potenti. Sed at pellentesque dolor. Vivamus sed nibh nisl. Nunc tortor tellus, facilisis eget pretium vitae, porttitor quis libero.</p>
  <p>More to Come - Lorem ipsum dolor sit amet, consectetur adipiscing elit. Suspendisse justo velit, auctor ut pulvinar a, egestas non urna. Suspendisse potenti. Sed at pellentesque dolor.</p>
  <p>More to Come - Lorem ipsum dolor sit amet, consectetur adipiscing elit. Suspendisse justo velit, auctor ut pulvinar a, egestas non urna. Suspendisse potenti. Sed at pellentesque dolor. Vivamus sed nibh nisl. Nunc tortor tellus, facilisis eget pretium vitae, porttitor quis libero.</p>
</div>
<p class="signoff"><strong>Dana Whitcombe</strong>Brisk Lantern Studio (.example)<br>(555) 014-2368</p>
<h2 class="back-title">Brisk Lantern<br>Marketing</h2>
<address class="office" style="left:444px;font-style:normal">Brisk Lantern Studio, LLC<br>48 Harbor Lane<br>Fairhollow, MA 01000<br>(555) 014-2368 x701</address>
<address class="office" style="right:442px;text-align:right;font-style:normal;top:818px">New Hampshire Office<br>902 Millbrook Road #12<br>Eastmere, NH 03000</address>

<h1 class="front-title">Brisk Lantern<br>Marketing</h1>
<p class="pitch">
  <span class="line">I Can Help You Get</span>
  <b>BETTER RESULTS</b>
  <span class="line">from Your Website, More Traffic,</span>
  <b>TOP RANKINGS</b>
  <span class="line">at Quorble, More Leads and</span>
  <b>MORE SALES.</b>
</p>
<p class="teaser">But first you'll have to avoid these<br>common Internet marketing myths...</p>
<p class="front-contact">Brisk Lantern Studio (.example)<br>(555) 014-2368<span class="front-url">www.brisklanternstudio.example</span></p>
</main>
</body>
</html>
```